Website Design for Solar Panel Company

We are working with a company called VoltaNix.

Some sites to use for content/competitors and inspiration:
https://www.brivaloo.com
https://prod.aws-prod.kelmatrix.com
https://tovarqueworks.net
https://www.quorvex.com/solarpanels

Thank you for taking the time to consider designing a website for us. We are web developers based in Stockton, CA, USA. Most of our projects go through the same process. Understanding this process may help you win a project with us. We custom-code all of our websites in-house. We don’t have any requirements as to what tools you use for your design, but we prefer Figma files. For any design that we label as four-stars, we send it to the client for review. The client picks the final design they want us to use. Once we complete this process, we will continue to show additional clients all the four-star sites and purchase them later. Your designs will have multiple chances to sell. For better chances of success, we ask that you follow these guidelines.

IMAGES:
If you use any images or icons in the design, we ask that you have a link to the asset so we can purchase the image/icon. Most of the designs we submit do not have the customer’s images on them unless they have some great images. Be creative; show us the feeling you are trying to portray with your image choices. Use any royalty-free site you choose. We subscribe to Pendrel and mainly use their images, but we can purchase images outside of Pendrel. PLEASE NOTE: we will not submit designs to clients with watermarks on the images.

FONTS:
We ask that you identify the fonts used in the design. This can be done in a message if you want. We typically use Google Fonts and Pendrel Fonts.

CONTENT:
We're always open to different content and ideas. We often submit designs with stock images so the client can see our vision. We typically take pictures after the website launch to use their images with our vision. Lorem Ipsum is fine for paragraphs, but we ask that you write the headers in correct English. We want to be able to show the vision and identify the sections of the website.

INSPIRATION:
We typically add a couple of links in the brief of websites we like to help you get started in your design.

REVISIONS:
We do not often ask for revisions of the designs unless we see something in the design that may not appeal to the client. If there are slight changes that we want to make, we do that in the development process.

FEEDBACK:
We rarely give feedback on designs during the design process. We are working on many website projects and do not have the time to provide feedback. We usually respond if your request is well thought out and asks specific questions, but a note asking “feedback, please” usually goes unanswered.

```html
<!DOCTYPE html>
<html lang="en">
<head>
<meta charset="utf-8">
<title>VoltaNix Energy Group</title>
<link href="https://fonts.googleapis.com/css2?family=Poppins:wght@500;600;700;800&family=Jost:wght@400;500;600&display=swap" rel="stylesheet">
<style>
:root{
  --green:#4fc51d;
  --green-light:#72e034;
  --green-dark:#2f9b12;
  --black:#000;
  --charcoal:#151515;
  --white:#fff;
  --field:#f4f4f4;
  --muted:#cfcfcf;
  --sky-a:#4d79b3;
  --sky-b:#a9bfd8;
}
*{box-sizing:border-box;margin:0;padding:0}
html,body{width:1200px;height:4467px;overflow:hidden}
body{background:var(--black);color:var(--white);font-family:'Jost',sans-serif;position:relative}
.heading{font-family:'Poppins',sans-serif;font-weight:700;text-transform:uppercase;letter-spacing:-0.5px}
.abs{position:absolute}
.btn{position:absolute;display:flex;align-items:center;justify-content:center;gap:10px;font-family:'Poppins',sans-serif;font-weight:600;text-transform:uppercase;font-size:15px;color:var(--white)}
.btn svg{width:20px;height:12px}
.btn-green{background:var(--green)}
.btn-black{background:var(--black)}
.underline{position:absolute;height:4px;background:var(--green)}

/* header */
.site-header{position:absolute;left:0;top:0;width:1200px;height:115px;background:var(--black)}
.topbar{position:absolute;right:0;top:0;width:602px;height:43px;background:var(--green);clip-path:polygon(0 0,100% 0,100% 100%,38px 100%)}
.topbar-item{position:absolute;top:11px;font-size:14px;display:flex;align-items:center;gap:10px}
.logo{position:absolute;text-align:left;font-family:'Poppins',sans-serif;font-weight:800;color:var(--white);line-height:1}
.logo-name{display:block}
.logo-sub{display:block;font-family:'Jost',sans-serif;font-weight:400;letter-spacing:0.5px}
.main-nav a{position:absolute;top:70px;color:var(--white);text-decoration:none;font-size:20px;font-weight:500}
/* hero */
.hero{position:absolute;left:0;top:115px;width:1200px;height:655px}
.hero-title{position:absolute;top:165px;width:100%;text-align:center;font-size:62px}
.hero-text{position:absolute;top:268px;width:100%;text-align:center;font-size:19px;line-height:25px}
/* about */
.about{position:absolute;left:0;top:770px;width:1200px;height:567px;background:var(--black)}
.photo-circle{position:absolute;border-radius:50%}
.body-text{font-size:13.5px;line-height:18px;color:#e8e8e8}
/* why */
.why{position:absolute;left:0;top:1337px;width:1200px;height:610px;background:var(--charcoal)}
.card-photo{position:absolute;width:294px;height:228px}
.card-label{position:absolute;background:var(--white);color:#222;font-family:'Poppins',sans-serif;font-weight:500;font-size:14px;text-transform:uppercase;height:54px;display:flex;align-items:center;justify-content:center}
/* quote */
.quote{position:absolute;left:0;top:1947px;width:1200px;height:611px;background:linear-gradient(115deg,#2a9a14 0%,#45b923 40%,#6ddd33 100%)}
.field{position:absolute;background:var(--field);border-radius:4px;color:#666;font-size:15px;padding:0 18px;display:flex;align-items:center}
/* high tech */
.hightech{position:absolute;left:0;top:2558px;width:1200px;height:639px;background:var(--black)}
.feature{position:absolute;left:98px;width:484px;height:62px;display:flex;align-items:center;gap:18px;font-size:16px}
.feature+.feature{border-top:1px solid #555}
/* faq */
.faq{position:absolute;left:0;top:3197px;width:1200px;height:544px;background:var(--charcoal)}
.faq-item{position:absolute;display:flex;align-items:center;gap:14px;font-size:16px;color:#e6e6e6}
/* cta */
.cta{position:absolute;left:0;top:3741px;width:1200px;height:316px;background:linear-gradient(115deg,#2a9a14 0%,#48bc25 45%,#6ddd33 100%)}
/* footer */
.site-footer{position:absolute;left:0;top:4057px;width:1200px;height:410px;background:var(--charcoal)}
.footer-nav{position:absolute;top:207px;left:0;width:1200px;display:flex;justify-content:center}
.footer-nav a{color:var(--white);text-decoration:none;font-size:20px;font-weight:500;padding:8px 25px;border-left:2px solid var(--green)}
.footer-nav a:first-child{border-left:none}
.footer-contact{position:absolute;top:292px;font-size:17px;display:flex;align-items:center;gap:14px}
.copyright{position:absolute;top:350px;width:100%;text-align:center;font-size:10px;color:#ddd}
</style>
</head>
<body>

<header class="site-header">
  <div class="topbar">
    <div class="topbar-item" style="left:250px">
      <svg width="14" height="14" viewBox="0 0 24 24"><path fill="#fff" d="M6.6 10.8c1.4 2.8 3.8 5.1 6.6 6.6l2.2-2.2c.3-.3.7-.4 1-.2 1.1.4 2.3.6 3.6.6.6 0 1 .4 1 1V20c0 .6-.4 1-1 1C10.6 21 3 13.4 3 4c0-.6.4-1 1-1h3.5c.6 0 1 .4 1 1 0 1.3.2 2.5.6 3.6.1.3 0 .7-.2 1z"/></svg>
      <span>888 888 8888</span>
    </div>
    <div class="topbar-item" style="left:418px">
      <svg width="16" height="12" viewBox="0 0 16 12"><rect width="16" height="12" rx="1" fill="#fff"/><path d="M1 1l7 5 7-5" stroke="#4fc51d" stroke-width="1.5" fill="none"/></svg>
      <span>info@domain.com</span>
    </div>
  </div>
  <div class="logo" style="left:33px;top:16px">
    <span class="logo-name" style="font-size:52px">VOLTANIX</span>
    <span class="logo-sub" style="font-size:30px;margin-top:2px">ENERGY GROUP</span>
  </div>
  <nav class="main-nav">
    <a style="left:370px">HOME</a>
    <a style="left:489px">ABOUT US</a>
    <a style="left:640px">SERVICES</a>
    <a style="left:799px">PRICES</a>
    <a style="left:919px">FAQS</a>
  </nav>
  <div class="btn btn-green" style="left:1027px;top:65px;width:145px;height:36px;font-size:14px;font-weight:500">Contact Us
    <svg viewBox="0 0 20 12"><path d="M0 6h16M12 1l6 5-6 5" stroke="#fff" stroke-width="2.4" fill="none"/></svg>
  </div>
</header>

<section class="hero">
  <svg class="abs" style="left:0;top:0" width="1200" height="655" viewBox="0 0 1200 655">
    <defs>
      <linearGradient id="heroSky" x1="0" y1="0" x2="1" y2="1">
        <stop offset="0" stop-color="#7f9ec4"/>
        <stop offset="0.45" stop-color="#3d6aa6"/>
        <stop offset="1" stop-color="#1e3f73"/>
      </linearGradient>
      <linearGradient id="heroGreen" x1="0" y1="0" x2="1" y2="0">
        <stop offset="0" stop-color="#2f9b12"/>
        <stop offset="1" stop-color="#5fd22a"/>
      </linearGradient>
    </defs>
    <path fill="url(#heroGreen)" d="M0 540 C120 590 350 640 600 648 C820 652 1060 580 1200 375 V500 C1060 630 820 700 600 705 C350 700 120 640 0 600 Z" transform="translate(0,-35)"/>
    <path role="img" aria-label="Technician in hard hat inspecting rows of solar panels under a blue sky" fill="url(#heroSky)" d="M0 0 H1200 V370 C1050 520 820 600 600 598 C350 592 120 540 0 490 Z"/>
  </svg>
  <h1 class="heading hero-title">VoltaNix Energy Group</h1>
  <p class="hero-text">Lorem ipsum dolor sit amet, consectetur adipiscing elit, sed do eiusmod<br>tempor incididunt ut labore et dolore magna aliqua.</p>
  <div class="btn btn-black" style="left:466px;top:355px;width:221px;height:46px;font-size:21px">Get a Quote
    <svg viewBox="0 0 20 12"><path d="M0 6h16M12 1l6 5-6 5" stroke="#4fc51d" stroke-width="2.6" fill="none"/></svg>
  </div>
</section>

<section class="about">
  <div class="photo-circle" role="img" aria-label="Solar engineer in hard hat standing at a solar farm with a colleague" style="left:112px;top:102px;width:400px;height:400px;background:linear-gradient(160deg,#b9c7d6 0%,#5a6f86 45%,#1f3556 75%,#e0e4ea 100%)"></div>
  <h2 class="heading abs" style="left:576px;top:168px;font-size:44px">About Us</h2>
  <div class="underline" style="left:576px;top:222px;width:70px"></div>
  <p class="body-text abs" style="left:576px;top:236px;width:545px">Lorem ipsum dolor sit amet, consectetur adipiscing elit, sed do eiusmod tempor incididunt ut labore et doloremagna aliqua. Ut enim ad minim veniam, quis nostrud exercitation ullamco laboris nisi ut aliquip ex ea commodo consequat. Duis aute irure dolor in reprehenderit in voluptate velit esse cillum dolore eu fugiat nulla pariatur.</p>
  <p class="body-text abs" style="left:576px;top:326px;width:545px">Excepteur sint occaecat cupidatat non proident, sunt in culpa qui officia deserunt mollit anim id est laborum.</p>
  <div class="btn btn-green" style="left:583px;top:402px;width:165px;height:40px">Get a Quote
    <svg viewBox="0 0 20 12"><path d="M0 6h16M12 1l6 5-6 5" stroke="#fff" stroke-width="2.4" fill="none"/></svg>
  </div>
</section>

<section class="why">
  <h2 class="heading abs" style="top:76px;width:100%;text-align:center;font-size:42px">Why Choose Us</h2>
  <div class="underline" style="left:546px;top:133px;width:114px"></div>
  <div class="card-photo" role="img" aria-label="Rooftop solar panels on a home" style="left:88px;top:190px;background:linear-gradient(160deg,#8d97a6,#3c4556 55%,#c4c8cc)"></div>
  <div class="card-label" style="left:120px;top:390px;width:228px">Unrivaled Home Solar</div>
  <div class="card-photo" role="img" aria-label="Robot holding a solar panel against a bright sky over grass" style="left:448px;top:195px;background:linear-gradient(180deg,#1c8ed0 0%,#6cc3ec 55%,#d9f2fb 75%,#5cbf3a 100%)"></div>
  <div class="card-label" style="left:486px;top:393px;width:228px">Smart Technology</div>
  <div class="card-photo" role="img" aria-label="Hands assembling a solar panel on a workbench" style="left:808px;top:195px;background:linear-gradient(160deg,#c59a6e 0%,#9a7657 35%,#2c2c2c 70%,#bdbdbd 100%)"></div>
  <div class="card-label" style="left:846px;top:393px;width:228px">Seamless Backup Power</div>
  <div class="btn btn-green" style="left:495px;top:520px;width:192px;height:40px">More About Us
    <svg viewBox="0 0 20 12"><path d="M0 6h16M12 1l6 5-6 5" stroke="#fff" stroke-width="2.4" fill="none"/></svg>
  </div>
</section>

<section class="quote">
  <h2 class="heading abs" style="top:62px;width:100%;text-align:center;font-size:42px">Get a Quote</h2>
  <div class="underline" style="left:532px;top:116px;width:144px;background:var(--white)"></div>
  <div class="field" style="left:231px;top:181px;width:352px;height:44px">Your Name</div>
  <div class="field" style="left:620px;top:181px;width:351px;height:44px">Your Phone</div>
  <div class="field" style="left:231px;top:254px;width:352px;height:44px">Email Address</div>
  <div class="field" style="left:620px;top:254px;width:351px;height:44px">Select Service</div>
  <div class="field" style="left:231px;top:325px;width:740px;height:93px;align-items:flex-start;padding-top:14px">Additional Message</div>
  <div class="btn btn-black" style="left:228px;top:446px;width:740px;height:55px;font-size:16px">Get a Free Quote Now</div>
</section>

<section class="hightech">
  <h2 class="heading abs" style="left:88px;top:190px;font-size:42px">High Tech. Hassle Free</h2>
  <p class="body-text abs" style="left:88px;top:258px;width:540px">Lorem ipsum dolor sit amet, consectetur adipiscing elit, sed do eiusmod tempor incididunt ut labore et doloremagna aliqua. Ut enim ad minim veniam, quis nostrud exercitation ullamco laboris nisi ut aliquip ex ea commodo consequat.</p>
  <div class="feature" style="top:324px">
    <svg width="28" height="28" viewBox="0 0 28 28"><circle cx="14" cy="11" r="8" fill="none" stroke="#4fc51d" stroke-width="2"/><circle cx="14" cy="11" r="3.5" fill="#4fc51d"/><path d="M9 18l-2 8 7-3 7 3-2-8" fill="none" stroke="#4fc51d" stroke-width="2"/></svg>
    <span>Best-in-class solar panels and battery storage</span>
  </div>
  <div class="feature" style="top:386px">
    <svg width="28" height="28" viewBox="0 0 28 28"><circle cx="14" cy="14" r="6" fill="none" stroke="#4fc51d" stroke-width="2"/><path d="M14 2v5M14 21v5M2 14h5M21 14h5M5.5 5.5l3.5 3.5M19 19l3.5 3.5M5.5 22.5L9 19M19 9l3.5-3.5" stroke="#4fc51d" stroke-width="2"/></svg>
    <span>25-year equipment guarantee</span>
  </div>
  <div class="feature" style="top:448px">
    <svg width="28" height="28" viewBox="0 0 28 28"><path d="M6 14h16l4 10H2z" fill="none" stroke="#4fc51d" stroke-width="2"/><path d="M10 14l-2 10M18 14l2 10M4 19h20" stroke="#4fc51d" stroke-width="1.6"/><circle cx="20" cy="6" r="3" fill="#4fc51d"/></svg>
    <span>High tech equipments</span>
  </div>
  <div class="photo-circle" role="img" aria-label="Solar panel array among green trees" style="left:698px;top:137px;width:404px;height:404px;background:linear-gradient(175deg,#e9f0e6 0%,#6f9a5a 40%,#2f5f86 70%,#9fb4c9 100%)"></div>
</section>

<section class="faq">
  <h2 class="heading abs" style="left:68px;top:80px;font-size:42px">Frequently Asked Questions</h2>
  <div class="underline" style="left:68px;top:134px;width:118px"></div>
  <div class="faq-item" style="left:78px;top:216px"><svg width="44" height="44" viewBox="0 0 44 44"><circle cx="22" cy="22" r="22" fill="#4fc51d"/><path d="M18 12l10 10-10 10" stroke="#fff" stroke-width="2.4" fill="none"/></svg>Lorem ipsum dolor sit amet, consectetur adipiscing elit.</div>
  <div class="faq-item" style="left:640px;top:216px"><svg width="44" height="44" viewBox="0 0 44 44"><circle cx="22" cy="22" r="22" fill="#4fc51d"/><path d="M18 12l10 10-10 10" stroke="#fff" stroke-width="2.4" fill="none"/></svg>Lorem ipsum dolor sit amet, consectetur adipiscing elit.</div>
  <div class="faq-item" style="left:78px;top:303px"><svg width="44" height="44" viewBox="0 0 44 44"><circle cx="22" cy="22" r="22" fill="#4fc51d"/><path d="M18 12l10 10-10 10" stroke="#fff" stroke-width="2.4" fill="none"/></svg>Lorem ipsum dolor sit amet, consectetur adipiscing elit.</div>
  <div class="faq-item" style="left:640px;top:303px"><svg width="44" height="44" viewBox="0 0 44 44"><circle cx="22" cy="22" r="22" fill="#4fc51d"/><path d="M18 12l10 10-10 10" stroke="#fff" stroke-width="2.4" fill="none"/></svg>Lorem ipsum dolor sit amet, consectetur adipiscing elit.</div>
  <div class="faq-item" style="left:78px;top:391px"><svg width="44" height="44" viewBox="0 0 44 44"><circle cx="22" cy="22" r="22" fill="#4fc51d"/><path d="M18 12l10 10-10 10" stroke="#fff" stroke-width="2.4" fill="none"/></svg>Lorem ipsum dolor sit amet, consectetur adipiscing elit.</div>
  <div class="faq-item" style="left:640px;top:391px"><svg width="44" height="44" viewBox="0 0 44 44"><circle cx="22" cy="22" r="22" fill="#4fc51d"/><path d="M18 12l10 10-10 10" stroke="#fff" stroke-width="2.4" fill="none"/></svg>Lorem ipsum dolor sit amet, consectetur adipiscing elit.</div>
</section>

<section class="cta">
  <h2 class="heading abs" style="top:60px;width:100%;text-align:center;font-size:42px">Get Ready to Start?</h2>
  <div class="underline" style="left:530px;top:117px;width:114px;background:var(--white)"></div>
  <p class="abs" style="top:144px;width:100%;text-align:center;font-size:16px;line-height:21px">Lorem ipsum dolor sit amet, consectetur adipiscing elit, sed do eiusmod tempor<br>incididunt ut labore et doloremagna aliqua.</p>
  <div class="btn btn-black" style="left:499px;top:223px;width:191px;height:39px">Contact Us
    <svg viewBox="0 0 20 12"><path d="M0 6h16M12 1l6 5-6 5" stroke="#4fc51d" stroke-width="2.4" fill="none"/></svg>
  </div>
</section>

<footer class="site-footer">
  <div class="logo" style="left:0;top:78px;width:1200px;text-align:center">
    <span class="logo-name" style="font-size:56px">VOLTANIX</span>
    <span class="logo-sub" style="font-size:32px;margin-top:2px">ENERGY GROUP</span>
  </div>
  <nav class="footer-nav">
    <a>HOME</a><a>ABOUT US</a><a>SERVICES</a><a>PRICES</a><a>FAQS</a>
  </nav>
  <div class="footer-contact" style="left:416px">
    <svg width="16" height="16" viewBox="0 0 24 24"><path fill="#4fc51d" d="M6.6 10.8c1.4 2.8 3.8 5.1 6.6 6.6l2.2-2.2c.3-.3.7-.4 1-.2 1.1.4 2.3.6 3.6.6.6 0 1 .4 1 1V20c0 .6-.4 1-1 1C10.6 21 3 13.4 3 4c0-.6.4-1 1-1h3.5c.6 0 1 .4 1 1 0 1.3.2 2.5.6 3.6.1.3 0 .7-.2 1z"/></svg>
    <span>888 888 8888</span>
  </div>
  <div class="footer-contact" style="left:615px">
    <svg width="18" height="13" viewBox="0 0 16 12"><rect width="16" height="12" rx="1" fill="#4fc51d"/><path d="M1 1l7 5 7-5" stroke="#151515" stroke-width="1.5" fill="none"/></svg>
    <span>info@domain.com</span>
  </div>
  <p class="copyright">Copyright 2024 VoltaNix Energy Group. All Rights Reserved.</p>
</footer>

</body>
</html>
```